Realtor branding business card

modern, simple and self branding. Broker office logo needs to be used but not emphasized. Looking to brand myself

Target Market(s)

buyers, sellers and investors

Industry/Entity Type

Realtor

Contact Information for Business Card

Sample of my current business card on file

Requirements
Must have
• my website - tobiasmerrowkl.com
• Realtor logo
• Fair housing logo
Nice to have
• Colors from office logo but not a must
Should not have
• Do not want headshot

```html
<!DOCTYPE html>
<html lang="en">
<head>
<meta charset="utf-8">
<title>Tobias Merrow, Realtor – Business Card</title>
<link href="https://fonts.googleapis.com/css2?family=Roboto:wght@400;500;700&display=swap" rel="stylesheet">
<style>
  :root {
    --page-bg: #2b2c30;
    --paper: #eeeeef;
    --navy: #25225f;
    --red: #c9262b;
    --ink-grey: #4a4a55;
    --white: #f2f2f4;
    --badge: #b9b9c4;
  }
  * { margin: 0; padding: 0; box-sizing: border-box; }
  html, body { width: 1200px; height: 1200px; overflow: hidden; }
  body {
    background: var(--page-bg);
    font-family: "Roboto", Arial, sans-serif;
    position: relative;
  }
  .card {
    position: absolute;
    left: 246px;
    width: 708px;
    height: 404px;
    overflow: hidden;
  }
  .card--front { top: 166px; background: var(--paper); }
  .card--back { top: 628px; background: var(--navy); }

  .brokerage {
    position: absolute;
    right: 54px;
    top: 88px;
    font-size: 24px;
    font-weight: 700;
    line-height: 1.1;
    color: var(--navy);
    text-align: right;
  }

  .agent { position: absolute; left: 50px; top: 178px; }
  .agent__name { font-size: 28px; font-weight: 700; color: var(--navy); line-height: 1.1; }
  .agent__title { font-size: 16px; color: var(--ink-grey); margin-top: 3px; }

  .contact { position: absolute; left: 50px; top: 250px; list-style: none; }
  .contact__item {
    display: flex; align-items: center; gap: 10px;
    font-size: 16px; color: var(--ink-grey); height: 20.5px;
  }
  .contact__item--web { color: var(--navy); font-weight: 500; }
  .contact__icon { width: 12px; height: 12px; fill: none; stroke: var(--navy); stroke-width: 1.4; }

  .badges {
    position: absolute; right: 54px; top: 290px;
    display: flex; gap: 14px; align-items: center;
  }
  .badge { width: 40px; height: 40px; background: var(--badge); }
  .badge--circle { border-radius: 50%; }

  .address-band {
    position: absolute; left: 0; top: 356px;
    width: 100%; height: 30px;
    background: linear-gradient(to right, var(--navy) 0 85%, var(--red) 85% 100%);
  }
  .address-band__text {
    position: absolute; left: 50px; top: 5px;
    font-size: 16px; color: var(--white);
  }

  .star-field {
    position: absolute; right: 0; top: 0;
    width: 300px; height: 300px;
    background: radial-gradient(ellipse at 70% 40%, rgba(80, 80, 170, 0.55), rgba(60, 60, 150, 0.2) 55%, rgba(37, 34, 95, 0) 75%);
  }
  .back-brand {
    position: absolute; left: 0; right: 0; top: 172px;
    text-align: center;
    font-size: 46px; font-weight: 700; line-height: 1; letter-spacing: -0.5px;
    color: var(--white);
  }
  .back-web {
    position: absolute; left: 0; right: 0; top: 342px;
    text-align: center;
    font-size: 15px; letter-spacing: 2.5px; color: var(--white);
  }
  .back-web strong { font-weight: 700; }
</style>
</head>
<body>

<section class="card card--front">
  <div class="brokerage">Keystone Lane<br>Realty Group</div>

  <div class="agent">
    <div class="agent__name">Tobias Merrow, Pa</div>
    <div class="agent__title">Realtor</div>
  </div>

  <ul class="contact">
    <li class="contact__item">
      <svg class="contact__icon" viewBox="0 0 12 12"><path d="M2 1.5 L4 1.5 L5 4 L3.8 5 Q5 7.5 7 8.2 L8 7 L10.5 8 L10.5 10 Q6 11 3 7.5 Q1 5 2 1.5 Z"/></svg>
      407-555-0146
    </li>
    <li class="contact__item">
      <svg class="contact__icon" viewBox="0 0 12 12"><rect x="3" y="1" width="6" height="3"/><rect x="1.5" y="4" width="9" height="5"/><rect x="3" y="7.5" width="6" height="3.5"/></svg>
      407-555-0182
    </li>
    <li class="contact__item">
      <svg class="contact__icon" viewBox="0 0 12 12"><rect x="1" y="2.5" width="10" height="7"/><path d="M1 2.5 L6 6.5 L11 2.5"/></svg>
      merrowrealty@mailbox.com
    </li>
    <li class="contact__item contact__item--web">
      <svg class="contact__icon" viewBox="0 0 12 12"><circle cx="6" cy="6" r="5"/><ellipse cx="6" cy="6" rx="2.2" ry="5"/><path d="M1 6 H11"/></svg>
      www.tobiasmerrowkl.com
    </li>
  </ul>

  <div class="badges">
    <div class="badge" role="img" aria-label="Realtor association badge"></div>
    <div class="badge badge--circle" role="img" aria-label="Equal housing opportunity badge"></div>
  </div>

  <div class="address-band">
    <span class="address-band__text">85 Harbor Crest Ave., Linden Springs, FL 32000</span>
  </div>
</section>

<section class="card card--back">
  <div class="star-field" role="img" aria-label="Faint scattered star pattern decoration"></div>
  <div class="back-brand">Tobias Merrow<br>Realtor</div>
  <div class="back-web">www.<strong>tobiasmerrowkl</strong>.com</div>
</section>

</body>
</html>
```